brqnal new business card design project

we need a new business card design. you can view info about us @ brqnal-example.com. i have attached an example of our previous card with our previous name that we no longer use. We really liked the design, colors etc. look below to see more info about this project. it asks for a limited number of words. please see our website for more info about our compnay.

Target Market(s)

law enforcement

Contact Information for Business Card

i have uploaded an example of what we used before that we liked.

Font styles to use
Serif

```html
<!DOCTYPE html>
<html lang="en">
<head>
<meta charset="utf-8">
<title>brqnal business card</title>
<link rel="stylesheet" href="https://fonts.googleapis.com/css2?family=Source+Serif+4:wght@400;600;700&display=swap">
<style>
  :root {
    --backdrop: #5e3820;
    --kraft-light: #d9b98e;
    --kraft-mid: #c49a6a;
    --kraft-dark: #a87a4a;
    --ink: #1b1712;
    --brand-ink: #10202c;
    --rule: #6b5338;
  }
  * { margin: 0; padding: 0; box-sizing: border-box; }
  html, body { width: 1200px; height: 900px; overflow: hidden; }
  body {
    position: relative;
    background: var(--backdrop);
    font-family: "Source Serif 4", Georgia, serif;
    color: var(--ink);
  }
  .card {
    position: absolute;
    background: radial-gradient(ellipse at 45% 20%, var(--kraft-light) 0%, var(--kraft-mid) 55%, var(--kraft-dark) 100%);
    box-shadow: 3px 4px 8px rgba(0,0,0,0.45);
    text-align: center;
  }
  .card-back { left: 330px; top: 90px; width: 555px; height: 343px; }
  .card-front { left: 330px; top: 470px; width: 558px; height: 342px; }

  .contact-block { position: absolute; left: 0; right: 0; top: 65px; font-size: 16px; line-height: 20px; }
  .person-name { font-weight: 700; font-size: 21px; line-height: 24px; }
  .person-title { font-size: 16px; line-height: 18px; }
  .divider { width: 145px; height: 1px; background: var(--rule); }
  .divider-top { margin: 11px auto 12px; }
  .divider-bottom { margin: 17px auto 18px; }
  .contact-line b { font-weight: 700; }

  .brand-name {
    position: absolute; left: 0; right: 0; top: 140px;
    font-weight: 600; font-size: 56px; line-height: 64px;
    color: var(--brand-ink);
  }
  .tagline {
    position: absolute; left: 0; right: 0; top: 282px;
    font-weight: 700; font-size: 15px; line-height: 20px;
    color: var(--brand-ink);
  }
</style>
</head>
<body>
  <section class="card card-back">
    <div class="contact-block">
      <div class="person-name">DANIEL MORROW</div>
      <div class="person-title">Managing Director</div>
      <div class="divider divider-top"></div>
      <div class="contact-line"><b>P:</b> 555.303.0142</div>
      <div class="contact-line"><b>E:</b> info@brqnal-example.com</div>
      <div class="contact-line"><b>W:</b> www.brqnal-example.com</div>
      <div class="divider divider-bottom"></div>
      <div class="address">4125 Ridgeview Lane<br>Austin, TX 78701</div>
    </div>
  </section>

  <section class="card card-front">
    <div class="brand-name">BRQNAL</div>
    <div class="tagline">LAW ENFORCEMENT INNOVATION</div>
  </section>
</body>
</html>
```